Music Marketing Agency in need of a fully responsive website

Need a website for our music marketing agency with a nice Rev slider has the ability to take payments has a section with our work and client able to see case studies able to download our media kit in PDF can take appointments has social media and a careers upload section. Also want a prominent contact form. Nice and icons for music industry. I want them to be able to download a free Picsandra marketing download Very clean and not large icons or menu at the top very minimal menu bar this will have to go with our logo as well which I will add to order. I want this to be a membership oriented site. so there will be packages displayed or a membership form which they can use to sign up and need a login window. Also need to be able to put Tunevox playlist on the website. Save a section for past clients logos.Again this has to be a clean concept I would like pictures of Quellos such as an app promotion. Definitely want lots of flash words in bold letters across the pages when they scroll through new sections.
Updates

Need extra days to review

Target Market(s)

Urban Music

Coding

Coded - Design and coding required

Font styles to use
Serif

Colors

Designer to choose colors to be used in the design.

Requirements
Must have
• Please Add Logos attached at the Footer

```html
<!DOCTYPE html>
<html lang="en">
<head>
<meta charset="utf-8">
<title>Velvet Arc Media – Member Login</title>
<link href="https://fonts.googleapis.com/css2?family=Montserrat:wght@500;600&family=Open+Sans:wght@400;600&display=swap" rel="stylesheet">
<style>
:root{
  --header-bg:#2a2a2a;
  --nav-text:#c9c9c9;
  --stage-bg:#e5e5e5;
  --card-bg:#ffffff;
  --input-bg:#efefef;
  --brand-blue:#2c4a9a;
  --footer-bg:#15245e;
  --footer-link:#7f97d8;
  --circle:#5a72b4;
  --rule:#3d5aa0;
  --text-dark:#111111;
  --text-mid:#555555;
  --white:#ffffff;
}
*{margin:0;padding:0;box-sizing:border-box}
html,body{width:1200px;height:884px;overflow:hidden}
body{font-family:"Open Sans",sans-serif;background:var(--stage-bg);position:relative}
a{text-decoration:none;color:inherit}

.site-header{position:absolute;left:0;top:0;width:1200px;height:70px;background:var(--header-bg)}
.site-name{position:absolute;left:131px;top:15px;font-family:"Open Sans",sans-serif;font-weight:600;font-size:31px;color:var(--white)}
.main-nav{position:absolute;right:133px;top:28px;display:flex;gap:27px;font-size:10.5px;color:var(--nav-text)}

.login-stage{position:absolute;left:0;top:70px;width:1200px;height:472px;background:var(--stage-bg)}
.login-card{position:absolute;left:487px;top:95px;width:226px;height:282px;background:var(--card-bg);box-shadow:0 1px 3px rgba(0,0,0,.12);text-align:center}
.card-name{margin-top:20px;font-family:"Montserrat",sans-serif;font-weight:600;font-size:16px;color:var(--text-dark)}
.card-title{margin-top:5px;font-family:"Montserrat",sans-serif;font-weight:600;font-size:24px;color:var(--brand-blue)}
.field{display:block;margin:12px auto 0;width:191px;height:35px;background:var(--input-bg);padding-left:15px;text-align:left;font-size:12px;line-height:35px;color:var(--text-mid)}
.field + .field{margin-top:13px}
.login-btn{display:block;margin:13px auto 0;width:191px;height:35px;background:var(--brand-blue);color:var(--white);font-weight:600;font-size:13px;line-height:35px}
.card-links{margin-top:15px;font-size:11.5px;line-height:19px;color:var(--text-mid)}

.site-footer{position:absolute;left:0;top:542px;width:1200px;height:342px;background:var(--footer-bg);color:var(--footer-link)}
.footer-heading{position:absolute;top:68px;font-family:"Montserrat",sans-serif;font-weight:500;font-size:16px;color:var(--white);letter-spacing:0.2px}
.footer-list{position:absolute;top:100px;list-style:none;font-size:10.5px;line-height:20.8px}
.badge{position:absolute;width:42px;height:42px;border-radius:50%;background:var(--circle);color:var(--white);font-size:7px;font-weight:600;display:flex;align-items:center;justify-content:center}
.footer-rule{position:absolute;left:132px;top:269px;width:936px;height:1px;background:var(--rule)}
.copyright{position:absolute;left:0;top:298px;width:1200px;text-align:center;font-size:11.5px;color:var(--footer-link)}
</style>
</head>
<body>
<header class="site-header">
  <div class="site-name">Velvet Arc Media</div>
  <nav class="main-nav">
    <a>Home</a><a>About Us</a><a>Services</a><a>Case Studies</a><a>Process</a><a>Work</a><a>Blog</a><a>Contact</a>
  </nav>
</header>

<section class="login-stage">
  <div class="login-card">
    <div class="card-name">Velvet Arc Media</div>
    <div class="card-title">Member Login</div>
    <div class="field">Username</div>
    <div class="field">Password</div>
    <a class="login-btn">LOGIN</a>
    <div class="card-links"><a>Forgot Password</a><br><a>Register Now</a></div>
  </div>
</section>

<footer class="site-footer">
  <h3 class="footer-heading" style="left:131px">FOLLOW US ON</h3>
  <div class="badge" style="left:132px;top:104px">Folio</div>
  <div class="badge" style="left:180px;top:104px">Chirpa</div>
  <div class="badge" style="left:228px;top:104px">Picsandra</div>
  <div class="badge" style="left:132px;top:152px">Vidora</div>
  <div class="badge" style="left:180px;top:152px">Tunevox</div>
  <div class="badge" style="left:228px;top:152px">
    <svg width="16" height="16" viewBox="0 0 16 16" aria-label="Share"><g fill="#fff"><circle cx="4" cy="8" r="2.6"/><circle cx="12" cy="3.5" r="2.6"/><circle cx="12" cy="12.5" r="2.6"/></g><path d="M4 8L12 3.5M4 8l8 4.5" stroke="#fff" stroke-width="1.6"/></svg>
  </div>

  <h3 class="footer-heading" style="left:341px">LINKS</h3>
  <ul class="footer-list" style="left:342px"><li>Home</li><li>About Us</li><li>Services</li><li>Case studies</li><li>Process</li><li>Work</li></ul>
  <ul class="footer-list" style="left:430px;top:98px"><li>Blog</li><li>Contact</li></ul>

  <h3 class="footer-heading" style="left:533px">NULLA FACILISI</h3>
  <ul class="footer-list" style="left:534px"><li>Etiam vel massa</li><li>Curabitur venenatis</li><li>Aliquam erat</li><li>Quisque aliquet</li><li>Pellentesque convallis</li><li>Etiam id</li></ul>

  <h3 class="footer-heading" style="left:725px">VIVAMUS LACUS</h3>
  <ul class="footer-list" style="left:726px"><li>Vivamus eleifend</li><li>Fusce vitae</li><li>Aenean placerat</li><li>Cras augue</li><li>Proin a dolor</li><li>Vestibulum eget</li></ul>

  <h3 class="footer-heading" style="left:930px">PAYMENTS</h3>
  <div class="badge" style="left:930px;top:104px">Vesta</div>
  <div class="badge" style="left:978px;top:104px">Paywell</div>
  <div class="badge" style="left:1026px;top:104px">Dexa</div>
  <div class="badge" style="left:930px;top:152px">Orbix</div>
  <div class="badge" style="left:978px;top:152px">Ledga</div>
  <div class="badge" style="left:1026px;top:152px">Circo</div>

  <div class="footer-rule"></div>
  <p class="copyright">Copyright &nbsp;©&nbsp; 2018 &nbsp;Velvet Arc Media. &nbsp; All rights reserved.</p>
</footer>
</body>
</html>
```